Harbourline Electrical Solutions

On one side. LOGO (underneath:) Commercial Industrial Residential

- NAME & CONTACT DETAILS

Marcus T. Hollings
Project Manager

(Cell icon) (441) 555-0187
(Email icon) hlelectricalsolutions@mailvento.com
(Facebook & Instagram icons )@hlelectricalsolutions

Other side: LOGO - underneath ELECTRICAL CONSTRUCTION & MAINTENANCE . LED LIGHTING & AUTOMATION . LIFE SAFETY SYSTEMS (FIRE ALARM / SECURITY) . DATA & COMMUNICATION

```html
<!DOCTYPE html>
<html lang="en">
<head>
<meta charset="utf-8">
<title>Harbourline Electrical Solutions – Business Card</title>
<link rel="stylesheet" href="https://fonts.googleapis.com/css2?family=Open+Sans:wght@400;600;700&display=swap">
<style>
  :root{
    --page:#e9e7e4;
    --card:#231f20;
    --teal:#1b6a86;
    --grey:#5a5859;
    --rule:#4c4a4b;
  }
  *{box-sizing:border-box;margin:0;padding:0}
  html,body{width:1200px;height:1200px;overflow:hidden}
  body{background:var(--page);font-family:"Open Sans",Arial,sans-serif;
    display:flex;flex-direction:column;align-items:center;justify-content:center;gap:44px}
  .card{width:900px;height:514px;background:var(--card);position:relative;
    box-shadow:0 6px 18px rgba(0,0,0,.18)}
  .brand{display:flex;align-items:center;gap:22px}
  .brand-mark{width:58px;height:58px;background:var(--teal)}
  .brand-name{color:var(--teal);font-weight:600;font-size:27px;line-height:1.12;
    letter-spacing:.2em;text-transform:uppercase}

  /* back side */
  .card--back .brand{position:absolute;left:230px;top:120px}
  .services{position:absolute;left:0;right:0;top:318px;text-align:center;
    color:var(--teal);font-size:19px;line-height:1.7;letter-spacing:.04em;text-transform:uppercase}
  .services .sep{color:var(--grey);padding:0 10px}

  /* front side */
  .card--front .brand{position:absolute;left:260px;top:58px}
  .sectors{position:absolute;left:0;right:0;top:190px;text-align:center;
    color:var(--grey);font-weight:600;font-size:22px;letter-spacing:.03em}
  .person{position:absolute;right:500px;top:268px;text-align:right}
  .person-name{color:var(--teal);font-weight:700;font-size:26px}
  .person-role{color:var(--grey);font-size:15px;margin-top:4px}
  .divider{position:absolute;left:430px;top:262px;width:2px;height:92px;background:var(--rule)}
  .contacts{position:absolute;left:460px;top:270px;list-style:none;color:var(--grey);font-size:20px}
  .contacts li{display:flex;align-items:center;gap:14px;margin-bottom:12px}
  .contacts svg{width:22px;height:22px;flex:none}
  .social{position:absolute;left:0;right:0;bottom:52px;display:flex;justify-content:center;
    align-items:center;gap:16px;color:var(--teal);font-weight:600;font-size:20px}
  .social-dot{width:38px;height:38px;border-radius:50%;background:var(--teal)}
</style>
</head>
<body>

<section class="card card--back" aria-label="Card back">
  <div class="brand">
    <span class="brand-mark"></span>
    <span class="brand-name">Harbourline<br>Electrical<br>Solutions</span>
  </div>
  <p class="services">
    Electrical Construction &amp; Maintenance<span class="sep">|</span>LED Lighting &amp; Automation<br>
    Life Safety Systems (Fire Alarm / Security)<span class="sep">|</span>Data &amp; Communication
  </p>
</section>

<section class="card card--front" aria-label="Card front">
  <div class="brand">
    <span class="brand-mark"></span>
    <span class="brand-name">Harbourline<br>Electrical<br>Solutions</span>
  </div>
  <p class="sectors">Commercial Industrial Residential</p>

  <div class="person">
    <p class="person-name">Marcus T. Hollings</p>
    <p class="person-role">Project Manager</p>
  </div>
  <span class="divider"></span>
  <ul class="contacts">
    <li>
      <svg viewBox="0 0 24 24" fill="none" stroke="#5a5859" stroke-width="1.6"><rect x="7" y="2.5" width="10" height="19" rx="1.8"/><line x1="11" y1="18.5" x2="13" y2="18.5"/></svg>
      (441) 555-0187
    </li>
    <li>
      <svg viewBox="0 0 24 24" fill="none" stroke="#5a5859" stroke-width="1.6"><rect x="2.5" y="5.5" width="19" height="13"/><polyline points="2.5,5.5 12,13 21.5,5.5"/></svg>
      hlelectricalsolutions@mailvento.com
    </li>
  </ul>

  <div class="social">
    <span>@hlelectricalsolutions</span>
    <span class="social-dot"></span>
    <span class="social-dot"></span>
    <span>@hlelectricalsolutions</span>
  </div>
</section>

</body>
</html>
```